Stationery & Envelope Design

Executive Style looking stationery & envelope design.
Business Information:
Larkspur Home Group
2875 Birchwood Lane, Fairbrook, CA 95661-4180
Phone: 916.555.0142
Fax: 916.555.0187

Industry/Entity Type

Business

```html
<!DOCTYPE html>
<html lang="en">
<head>
<meta charset="utf-8">
<title>Larkspur Home Group — Stationery &amp; Envelopes</title>
<link href="https://fonts.googleapis.com/css2?family=Arimo:wght@400;700&display=swap" rel="stylesheet">
<style>
  :root{
    --backdrop:#d8cbb6;
    --paper:#ffffff;
    --brand-blue:#0d4f9e;
    --brand-navy:#1f3f7a;
    --brand-green:#7a8a36;
    --ink:#222222;
    --rule:#2b2b2b;
    --edge:#b9b9b9;
    --grey:#555555;
  }
  *{margin:0;padding:0;box-sizing:border-box}
  html,body{width:1200px;height:1089px;overflow:hidden}
  body{background:var(--backdrop);font-family:"Arimo",Arial,sans-serif;color:var(--ink);position:relative}

  .fax-sheet{position:absolute;top:40px;width:471px;height:610px;background:var(--paper);box-shadow:0 1px 3px rgba(0,0,0,.35);overflow:hidden}
  .fax-sheet--left{left:83px}
  .fax-sheet--right{left:618px}

  .sheet-corner{position:absolute;left:0;top:0}
  .brand-name{position:absolute;left:35px;top:60px;font-weight:400;font-size:18px;color:var(--brand-blue);white-space:nowrap}
  .brand-dot{position:absolute;left:35px;top:40px;width:14px;height:14px;border-radius:50%;background:var(--brand-green)}

  .sender-block{position:absolute;left:341px;top:30px;padding-left:6px;border-left:1px solid #9a9a9a;font-size:7.6px;line-height:11px;color:var(--ink);font-style:normal}
  .sender-block .sender-name{color:var(--brand-green);font-size:8.6px}

  .fax-title{position:absolute;left:35px;top:128px;font-size:29px;font-weight:400;color:var(--ink)}

  .fax-fields{position:absolute;left:39px;top:192px;width:392px}
  .fax-row{position:relative;height:55.5px;border-bottom:1.6px solid var(--rule)}
  .fax-row:first-child{height:21px}
  .fax-label{position:absolute;bottom:9px;font-size:10.5px;color:var(--ink)}
  .fax-label--right{left:254px}

  .sheet-footer{position:absolute;left:0;bottom:0}
  .footer-contact{position:absolute;right:14px;bottom:9px;color:#fff;font-size:8.6px;line-height:13px;text-align:right}
  .footer-contact span{display:inline-flex;align-items:center;gap:3px;margin-left:6px}
  .footer-contact--stacked span{display:flex;justify-content:flex-end;margin-left:0}

  .envelope-set{position:absolute;left:0;top:0}
  .env-name{font-family:"Arimo",Arial,sans-serif;font-weight:400;font-size:16px;text-anchor:middle}
  .env-address{font-family:"Arimo",Arial,sans-serif;font-size:7px;fill:var(--ink)}
</style>
</head>
<body>

<section class="fax-sheet fax-sheet--left">
  <svg class="sheet-corner" width="140" height="60" viewBox="0 0 140 60">
    <path d="M0 44 C22 20 62 6 130 2 C70 8 30 22 0 50 Z" fill="var(--brand-blue)"/>
    <path d="M0 54 C25 28 70 10 140 4 C75 14 32 30 0 60 Z" fill="var(--brand-green)"/>
  </svg>
  <span class="brand-dot"></span>
  <div class="brand-name">Larkspur Home Group</div>
  <address class="sender-block">
    <div class="sender-name">Larkspur Home Group</div>
    <div>2875 Birchwood Lane</div>
    <div>Fairbrook, CA 95661-4180</div>
  </address>
  <h1 class="fax-title">FAX</h1>
  <div class="fax-fields">
    <div class="fax-row"><span class="fax-label">To</span><span class="fax-label fax-label--right">From</span></div>
    <div class="fax-row"><span class="fax-label">Fax</span><span class="fax-label fax-label--right">Pages</span></div>
    <div class="fax-row"><span class="fax-label">Phone</span><span class="fax-label fax-label--right">Date</span></div>
    <div class="fax-row"><span class="fax-label">Re</span><span class="fax-label fax-label--right">CC</span></div>
  </div>
  <svg class="sheet-footer" width="471" height="62" viewBox="0 0 471 62">
    <path d="M0 62 L0 52 C140 50 300 22 471 4 L471 62 Z" fill="var(--brand-blue)"/>
    <path d="M0 30 C70 46 160 50 300 32 C180 56 80 54 0 42 Z" fill="var(--brand-green)"/>
    <path d="M40 40 C150 52 260 40 380 18" fill="none" stroke="var(--brand-navy)" stroke-width="1.2"/>
  </svg>
  <div class="footer-contact">
    <span><svg width="8" height="8" viewBox="0 0 10 10"><path d="M2 1 L4 1 L5 3 L4 4 C4.6 5.4 5.6 6.4 7 7 L8 6 L10 7 L10 9 C6 10 0 4 1 1 Z" fill="#fff"/></svg>916.555.0142</span>
    <span><svg width="9" height="8" viewBox="0 0 10 9"><rect x="2" y="0" width="6" height="3" fill="#fff"/><rect x="0" y="3" width="10" height="4" rx="1" fill="#fff"/><rect x="2" y="6" width="6" height="3" fill="#fff"/></svg>916.555.0187</span>
  </div>
</section>

<section class="fax-sheet fax-sheet--right">
  <svg class="sheet-corner" width="140" height="60" viewBox="0 0 140 60">
    <path d="M0 44 C22 20 62 6 130 2 C70 8 30 22 0 50 Z" fill="var(--brand-blue)"/>
    <path d="M0 54 C25 28 70 10 140 4 C75 14 32 30 0 60 Z" fill="var(--brand-green)"/>
  </svg>
  <span class="brand-dot"></span>
  <div class="brand-name">Larkspur Home Group</div>
  <address class="sender-block">
    <div class="sender-name">Larkspur Home Group</div>
    <div>2875 Birchwood Lane</div>
    <div>Fairbrook, CA 95661-4180</div>
  </address>
  <h1 class="fax-title">FAX</h1>
  <div class="fax-fields">
    <div class="fax-row"><span class="fax-label">To</span><span class="fax-label fax-label--right">From</span></div>
    <div class="fax-row"><span class="fax-label">Fax</span><span class="fax-label fax-label--right">Pages</span></div>
    <div class="fax-row"><span class="fax-label">Phone</span><span class="fax-label fax-label--right">Date</span></div>
    <div class="fax-row"><span class="fax-label">Re</span><span class="fax-label fax-label--right">CC</span></div>
  </div>
  <svg class="sheet-footer" width="471" height="62" viewBox="0 0 471 62">
    <path d="M0 62 L0 52 C140 50 300 22 471 4 L471 62 Z" fill="var(--brand-blue)"/>
    <path d="M0 30 C70 46 160 50 300 32 C180 56 80 54 0 42 Z" fill="var(--brand-green)"/>
    <path d="M40 40 C150 52 260 40 380 18" fill="none" stroke="var(--brand-navy)" stroke-width="1.2"/>
  </svg>
  <div class="footer-contact footer-contact--stacked">
    <span><svg width="8" height="8" viewBox="0 0 10 10"><path d="M2 1 L4 1 L5 3 L4 4 C4.6 5.4 5.6 6.4 7 7 L8 6 L10 7 L10 9 C6 10 0 4 1 1 Z" fill="#fff"/></svg>916.555.0142</span>
    <span><svg width="9" height="8" viewBox="0 0 10 9"><rect x="2" y="0" width="6" height="3" fill="#fff"/><rect x="0" y="3" width="10" height="4" rx="1" fill="#fff"/><rect x="2" y="6" width="6" height="3" fill="#fff"/></svg>916.555.0187</span>
  </div>
</section>

<svg class="envelope-set" width="1200" height="1089" viewBox="0 0 1102 1000">
  <defs>
    <linearGradient id="blueFlap" x1="0" x2="1" y1="0" y2="0">
      <stop offset="0" stop-color="#4c5f8c"/>
      <stop offset=".55" stop-color="#0d4f9e"/>
      <stop offset="1" stop-color="#0b4fa0"/>
    </linearGradient>
  </defs>

  <g class="envelope envelope--white-back">
    <rect x="72" y="620" width="483" height="210" fill="var(--paper)" stroke="var(--edge)"/>
    <path d="M72 620 L555 620 L541 686 L86 686 Z" fill="var(--paper)" stroke="var(--edge)"/>
    <text class="env-name" x="313" y="660" fill="var(--brand-green)">Larkspur Home Group</text>
  </g>
  <g class="envelope envelope--grey">
    <rect x="46" y="685" width="482" height="210" fill="var(--paper)" stroke="var(--edge)"/>
    <path d="M46 685 L528 685 L514 750 L60 750 Z" fill="var(--paper)" stroke="var(--edge)"/>
    <text class="env-name" x="287" y="723" fill="var(--grey)">Larkspur Home Group</text>
  </g>
  <g class="envelope envelope--front">
    <rect x="31" y="755" width="484" height="210" fill="var(--paper)" stroke="#333" stroke-width="1"/>
    <path d="M31 790 C48 772 78 760 125 756 C80 762 52 774 31 794 Z" fill="var(--brand-blue)"/>
    <path d="M31 800 C52 780 85 766 135 760 C90 770 58 782 31 806 Z" fill="var(--brand-green)"/>
    <circle cx="54" cy="790" r="6" fill="var(--brand-green)"/>
    <text x="48" y="814" font-family="Arimo, Arial, sans-serif" font-weight="400" font-size="13" fill="var(--brand-blue)">Larkspur Home Group</text>
    <text class="env-address" x="48" y="836">Larkspur Home Group, 2875 Birchwood Lane, Fairbrook, CA 95661-4180</text>
    <path d="M31 965 L31 955 C170 952 360 928 515 900 L515 965 Z" fill="var(--brand-blue)"/>
    <path d="M31 928 C110 944 220 946 340 930 C220 956 110 954 31 944 Z" fill="var(--brand-green)"/>
    <path d="M70 940 C180 950 300 938 420 920" fill="none" stroke="var(--brand-navy)" stroke-width="1"/>
  </g>

  <rect x="556" y="612" width="499" height="273" fill="var(--paper)" stroke="var(--edge)"/>
  <g class="envelope envelope--green">
    <path d="M571 612 L1054 612 L1040 690 L585 690 Z" fill="var(--brand-green)"/>
    <text class="env-name" x="812" y="657" fill="#ffffff">Larkspur Home Group</text>
  </g>
  <g class="envelope envelope--blue">
    <path d="M556 676 L1040 676 L1026 742 L570 742 Z" fill="url(#blueFlap)"/>
    <text class="env-name" x="798" y="714" fill="#ffffff">Larkspur Home Group</text>
  </g>
  <g class="envelope envelope--mono">
    <rect x="587" y="750" width="485" height="210" fill="var(--paper)" stroke="var(--edge)"/>
    <path d="M587 750 L1072 750 L1058 812 L601 812 Z" fill="var(--paper)" stroke="var(--edge)"/>
    <text class="env-name" x="830" y="789" fill="#000000">Larkspur Home Group</text>
  </g>
</svg>

</body>
</html>
```